Birchline Septic Solutions

Would like to see some single sided ones but would also like to see some double sided with one sided only being the logo. Owners name is Colin Vandro. Phone number is 555-214-0387
Services are pumping, inspections, installs, and repairs

Contact Information for Business Card

555-241-0387 Colin Vandro Ashbury, OH

```html
<!DOCTYPE html>
<html lang="en">
<head>
<meta charset="utf-8">
<title>Birchline Septic Solutions – Business Card</title>
<link rel="stylesheet" href="https://fonts.googleapis.com/css2?family=Montserrat:wght@500;600;700&display=swap">
<style>
  :root {
    --backdrop: #e9e2d8;
    --card-top: #f3f1ee;
    --card-bottom: #dfdad3;
    --card-edge: rgba(255, 255, 255, 0.85);
    --ink: #262626;
    --teal: #1aa795;
    --teal-light: #2cc4c4;
  }
  * { box-sizing: border-box; margin: 0; padding: 0; }
  html, body {
    width: 1200px;
    height: 897px;
    overflow: hidden;
    background: var(--backdrop);
    font-family: "Montserrat", sans-serif;
  }
  .business-card {
    position: absolute;
    left: 80px;
    top: 166px;
    width: 1040px;
    height: 565px;
    border-radius: 28px;
    background: linear-gradient(160deg, var(--card-top), var(--card-bottom));
    border: 2px solid var(--card-edge);
    box-shadow: 0 18px 40px rgba(60, 45, 30, 0.18);
  }
  .brand-name {
    position: absolute;
    left: 118px;
    top: 262px;
    width: 360px;
    text-align: center;
    color: var(--ink);
    font-weight: 700;
  }
  .brand-name .brand-main {
    display: block;
    font-size: 60px;
    letter-spacing: 1px;
    line-height: 1;
    text-transform: uppercase;
    white-space: nowrap;
  }
  .brand-name .brand-sub {
    display: block;
    margin-top: 22px;
    font-size: 17px;
    letter-spacing: 6px;
    text-transform: uppercase;
    white-space: nowrap;
  }
  .divider {
    position: absolute;
    left: 525px;
    top: 187px;
    width: 2px;
    height: 191px;
    background: var(--teal);
  }
  .contact {
    position: absolute;
    left: 568px;
    top: 202px;
    white-space: nowrap;
  }
  .owner-name {
    font-size: 46px;
    font-weight: 700;
    letter-spacing: 0.5px;
    line-height: 1;
    text-transform: uppercase;
    background: linear-gradient(90deg, var(--teal), var(--teal-light));
    -webkit-background-clip: text;
    background-clip: text;
    color: transparent;
  }
  .location {
    margin-top: 16px;
    font-size: 27px;
    font-weight: 600;
    letter-spacing: 1px;
    line-height: 1;
    color: var(--ink);
  }
  .phone {
    display: flex;
    align-items: center;
    gap: 16px;
    margin-top: 26px;
    font-size: 40px;
    font-weight: 500;
    letter-spacing: 1px;
    line-height: 1;
    color: var(--ink);
  }
  .phone-icon { width: 34px; height: 28px; flex: none; }
</style>
</head>
<body>
  <div class="business-card">
    <div class="brand-name">
      <span class="brand-main">Birchline</span>
      <span class="brand-sub">Septic Solutions</span>
    </div>
    <div class="divider"></div>
    <div class="contact">
      <p class="owner-name">Colin Vandro</p>
      <p class="location">Ashbury, OH</p>
      <p class="phone">
        <svg class="phone-icon" viewBox="0 0 34 28" aria-hidden="true">
          <path d="M2 9 C2 3 32 3 32 9 L32 12 L25 12 L25 8 L9 8 L9 12 L2 12 Z" fill="var(--teal)"/>
          <path d="M10 10 L24 10 L30 26 L4 26 Z" fill="var(--teal)"/>
          <circle cx="17" cy="18" r="4" fill="var(--card-top)"/>
        </svg>
        <span>555-241-0387</span>
      </p>
    </div>
  </div>
</body>
</html>
```